Financial Advisor Resource Firm needs business card design

Need business card design for company in Omaha NE called Meridale Circle. We provide resources to financial advisors....workshop programs, retirement analysis, and insurance planning. I would like to see designs that use grays, greens, black, and white colors. The final design should communicate 'collaboration' and be simple yet attractive to financial planning clients. I will attached our logo and another picture of a puzzle piece coming together. I would like the incorporate the puzzle picture somehow, maybe on the back somehow, with color or just the gray scale....OR, the picture be the front of the card with 'Meridale' definition on it (see upload) and then company logo, employee name, title, address on the back (see ppt uploaded). The following disclosure needs to be included somewhere- Advisory services offered through Stonebrook Assets, LLC.
Updates

I uploaded a svg and ai file of the logo

Target Market(s)

Financial planning clients and financial advisors....so pretty diverse age range of about 40-70.

Industry/Entity Type

Financial Planning

Contact Information for Business Card

Tobias L. Fenwright, MBA
Founder/President
5287 E. Larkin Road
Suite 410
Fairhaven, IA 50117
Phone- (402) 555-0147
Cell- (402) 555-0183
Fax- (402) 555-0129
email- tobias@meridaleplan.example
web address- www.meridaleplan.example

Colors
1b1b1b
474747
d3d3d3
ffffff
9bcb3c
abd036

Requirements
Must have
• Must include logo provided, must be 2 sided, and must have disclosure...all of these items listed in project description

```html
<!DOCTYPE html>
<html lang="en">
<head>
<meta charset="utf-8">
<title>Meridale Circle — Business Card</title>
<link rel="stylesheet" href="https://fonts.googleapis.com/css2?family=Lato:wght@400;700&family=Tinos&display=swap">
<style>
  :root {
    --backdrop: #3a3431;
    --card: #1b1b1b;
    --rule: #474747;
    --muted: #9a9a9a;
    --light: #d3d3d3;
    --white: #ffffff;
    --green: #9bcb3c;
    --green-soft: #abd036;
  }
  * { box-sizing: border-box; margin: 0; padding: 0; }
  html, body {
    width: 1200px; height: 844px; overflow: hidden;
    background: var(--backdrop);
    font-family: "Lato", Arial, sans-serif;
  }
  .stage {
    position: relative; width: 1200px; height: 844px;
    display: flex; align-items: center; justify-content: center; gap: 48px;
  }
  .card {
    width: 500px; height: 286px; background: var(--card);
    box-shadow: 0 10px 30px rgba(0,0,0,.45);
    position: relative;
  }

  /* Contact side */
  .card--contact { display: flex; align-items: center; }
  .brand-block {
    width: 210px; display: flex; flex-direction: column; align-items: center; gap: 14px;
  }
  .brand-block__ring {
    width: 96px; height: 96px; border-radius: 50%;
    border: 10px solid var(--green);
  }
  .brand-block__name {
    color: var(--white); font-weight: 700; font-size: 17px; letter-spacing: .5px;
  }
  .contact {
    border-left: 1px solid var(--rule);
    padding: 6px 0 6px 16px; height: 170px;
    display: flex; flex-direction: column; justify-content: center;
  }
  .contact__name {
    color: var(--green); font-weight: 700; font-size: 15px; text-transform: uppercase;
  }
  .contact__name small { font-size: 13px; color: var(--green-soft); }
  .contact__title { color: var(--muted); font-size: 12px; margin-bottom: 6px; }
  .contact__row {
    display: flex; align-items: center; gap: 7px;
    color: var(--muted); font-size: 12px; line-height: 17px;
  }
  .contact__row svg { width: 10px; height: 10px; fill: var(--green); flex: none; }
  .contact__address { color: var(--muted); font-size: 12px; line-height: 16px; margin-top: 4px; }

  /* Brand side */
  .card--brand { padding: 62px 34px 0 34px; }
  .wordmark {
    color: var(--light); font-weight: 700; font-size: 32px; letter-spacing: 3px;
    text-transform: uppercase;
  }
  .tagline {
    font-family: "Tinos", "Times New Roman", serif;
    color: var(--muted); font-size: 13px; margin-top: 10px;
    border-top: 1px solid var(--rule); padding-top: 8px;
  }
  .disclosure {
    position: absolute; left: 34px; right: 34px; bottom: 36px;
    border-top: 1px solid var(--rule); padding-top: 8px;
    color: var(--white); font-size: 11px; letter-spacing: .4px; text-transform: uppercase;
  }
</style>
</head>
<body>
<main class="stage">
  <section class="card card--contact" aria-label="Contact side">
    <div class="brand-block">
      <div class="brand-block__ring"></div>
      <div class="brand-block__name">Meridale Circle</div>
    </div>
    <div class="contact">
      <p class="contact__name">Tobias L. Fenwright, <small>MBA</small></p>
      <p class="contact__title">Founder/President</p>
      <p class="contact__row"><svg viewBox="0 0 10 10"><path d="M1 2c0-1 1-1.5 2-1.5l1 2-1 1c.6 1.3 1.4 2.1 2.5 2.5l1-1 2 1C8.5 7.5 8 9 7 9 3.5 9 1 6 1 2z"/></svg>(402) 555-0147</p>
      <p class="contact__row"><svg viewBox="0 0 10 10"><path d="M3 0h4a1 1 0 0 1 1 1v8a1 1 0 0 1-1 1H3a1 1 0 0 1-1-1V1a1 1 0 0 1 1-1zm0 1.5v6h4v-6z"/></svg>(402) 555-0183</p>
      <p class="contact__row"><svg viewBox="0 0 10 10"><path d="M2.5 0h5v3h-5zM0 3.5h10V8H8v2H2V8H0zm3 3V9h4V6.5z"/></svg>(402) 555-0129</p>
      <p class="contact__row"><svg viewBox="0 0 10 10"><path d="M0 2h10v6H0zm1 1v.3l4 2.4 4-2.4V3z"/></svg>tobias@meridaleplan.example</p>
      <p class="contact__row"><svg viewBox="0 0 10 10"><circle cx="5" cy="5" r="5"/></svg>www.meridaleplan.example</p>
      <p class="contact__address">5287 E. Larkin Road<br>Suite 410 Fairhaven, IA 50117</p>
    </div>
  </section>

  <section class="card card--brand" aria-label="Brand side">
    <h1 class="wordmark">Meridale Circle</h1>
    <p class="tagline">Where shared goals meet steady guidance and lasting trust</p>
    <p class="disclosure">Advisory services offered through Stonebrook Assets, LLC.</p>
  </section>
</main>
</body>
</html>
```